Business Cards for Internet Security Company

Awesome designers! This is the opportunity to help design cards for a forward thinking network security company. They use threat information gathered from peer groups to make intelligent decisions on what threats are relevant and which arent. ( not that you need this to do designs, but just so you know where they are coming from. ) :-)

We'd like to see a two side design and the deliverables will be in illustrator 4. The logo is attached and the logo colors are attached in the JPG and I've attached a an eps of the logo and icon

Security

```html
<!DOCTYPE html>
<html lang="en">
<head>
<meta charset="utf-8">
<title>Nexwall Business Card</title>
<link rel="stylesheet" href="https://fonts.googleapis.com/css2?family=Open+Sans:wght@400;600;700&display=swap">
<style>
  :root {
    --stage: #eceeef;
    --brand-blue: #1a5d9c;
    --brand-blue-light: #2a86d4;
    --card-white: #ffffff;
    --card-grey: #d3d5d7;
    --text-white: #ffffff;
    --text-soft: #dbe7f3;
  }
  * { margin: 0; padding: 0; box-sizing: border-box; }
  html, body {
    width: 1200px; height: 891px; overflow: hidden;
    background: var(--stage);
    font-family: "Open Sans", Arial, sans-serif;
  }
  .sheet {
    width: 1200px; height: 891px;
    display: flex; flex-direction: column; align-items: center; justify-content: center;
    gap: 56px;
  }
  .card {
    position: relative;
    width: 640px; height: 366px;
    overflow: hidden;
    box-shadow: 0 6px 18px rgba(0,0,0,0.18);
  }
  .card-art { position: absolute; inset: 0; width: 100%; height: 100%; }

  .brand {
    position: absolute; left: 58px; top: 96px;
    display: flex; align-items: center; gap: 14px;
  }
  .brand-dot {
    width: 46px; height: 46px; border-radius: 50%;
    background: var(--brand-blue-light);
  }
  .brand-name {
    font-size: 66px; font-weight: 400; line-height: 1;
    color: var(--brand-blue); letter-spacing: 0.5px;
  }

  .holder {
    position: absolute; left: 30px; top: 300px;
    color: var(--text-white);
  }
  .holder-name { font-size: 17px; font-weight: 700; letter-spacing: 0.6px; text-transform: uppercase; }
  .holder-role { font-size: 12px; font-weight: 400; color: var(--text-soft); margin-top: 2px; }

  .contacts {
    position: absolute; left: 372px; top: 166px;
    list-style: none; color: var(--text-white);
    font-size: 12px; line-height: 1;
  }
  .contacts li { display: flex; align-items: center; gap: 9px; margin-bottom: 11px; }
  .contacts svg { width: 12px; height: 12px; flex: none; }
</style>
</head>
<body>
<main class="sheet">

  <section class="card card-front" aria-label="Card front">
    <svg class="card-art" viewBox="0 0 640 366" preserveAspectRatio="none" aria-hidden="true">
      <defs>
        <linearGradient id="paper" x1="0" y1="0" x2="1" y2="1">
          <stop offset="0" stop-color="#ffffff"/>
          <stop offset="0.55" stop-color="#f1f2f3"/>
          <stop offset="1" stop-color="#d3d5d7"/>
        </linearGradient>
      </defs>
      <rect width="640" height="366" fill="url(#paper)"/>
      <!-- top rules -->
      <polygon points="0,22 396,22 388,32 0,32" fill="#1a5d9c"/>
      <polygon points="0,42 300,42 294,48 0,48" fill="#1a5d9c"/>
      <!-- contact panel -->
      <polygon points="370,148 640,148 640,366 262,366" fill="#1a5d9c"/>
      <!-- name panel -->
      <polygon points="0,284 232,284 196,366 0,366" fill="#1a5d9c"/>
      <!-- divider strokes -->
      <polygon points="240,284 252,284 216,366 204,366" fill="#1a5d9c"/>
      <polygon points="350,148 358,148 250,366 242,366" fill="#1a5d9c"/>
    </svg>

    <div class="brand">
      <span class="brand-dot"></span>
      <span class="brand-name">Nexwall</span>
    </div>

    <div class="holder">
      <p class="holder-name">Daniel Morrow</p>
      <p class="holder-role">Managing Director</p>
    </div>

    <ul class="contacts">
      <li><svg viewBox="0 0 12 12"><rect x="1.5" y="1.5" width="9" height="9" fill="none" stroke="#fff" stroke-width="1.3"/></svg>014 276 3310</li>
      <li><svg viewBox="0 0 12 12"><path d="M2 1.5l2.2 0 1 2.6-1.3 1a6 6 0 0 0 2.9 2.9l1-1.3 2.6 1v2.2c-5 .5-9-3.5-8.4-8.4z" fill="#fff"/></svg>014 276 3311</li>
      <li><svg viewBox="0 0 12 12"><rect x="1" y="2.5" width="10" height="7" fill="#fff"/><path d="M1 2.5l5 4 5-4" fill="none" stroke="#1a5d9c" stroke-width="1"/></svg>hello@nexwall.net</li>
      <li><svg viewBox="0 0 12 12"><circle cx="6" cy="6" r="4.8" fill="none" stroke="#fff" stroke-width="1.2"/><ellipse cx="6" cy="6" rx="2" ry="4.8" fill="none" stroke="#fff" stroke-width="1"/><line x1="1.2" y1="6" x2="10.8" y2="6" stroke="#fff" stroke-width="1"/></svg>www.nexwall.net</li>
      <li><svg viewBox="0 0 12 12"><path d="M6 11.5C3 7.8 2 6.2 2 4.5a4 4 0 0 1 8 0c0 1.7-1 3.3-4 7z" fill="#fff"/><circle cx="6" cy="4.5" r="1.4" fill="#1a5d9c"/></svg>27 Harbour Lane, 4th Floor, Elmstead</li>
    </ul>
  </section>

  <section class="card card-back" aria-label="Card back">
    <svg class="card-art" viewBox="0 0 640 366" preserveAspectRatio="none" aria-hidden="true">
      <rect width="640" height="366" fill="#1a5d9c"/>
      <polygon points="60,0 74,0 18,366 4,366" fill="#ffffff"/>
      <polygon points="88,0 96,0 40,366 32,366" fill="#ffffff"/>
      <polygon points="560,0 568,0 512,366 504,366" fill="#ffffff"/>
      <polygon points="582,0 596,0 540,366 526,366" fill="#ffffff"/>
    </svg>
  </section>

</main>
</body>
</html>
```